Harvest Gateway Fellowship Ministries needs a fresh new web design

We are an up and coming multicultural church that aims to bring people into a life changing encounter with God. We need a fresh and inviting website in order to increase our internet presence and make us easier to connect with.
Here are some of the basic requirements for the site:
• Clearly displayed address, service times, and contact info
• A staff profile page
• An area for a calendar with upcoming events and their details
• Social media buttons
• Group pages for the different ministries (youth, children’s church, men, etc…)
• An area for donations and eCommerce
• A resources page for assorted media (podcasts, sermons, videos, etc.…)
• An area for prayer requests.

```html
<!DOCTYPE html>
<html lang="en">
<head>
<meta charset="utf-8">
<title>Harvest Gateway Fellowship Ministries</title>
<link rel="stylesheet" href="https://fonts.googleapis.com/css2?family=Arimo:wght@400;700&family=Noto+Serif&family=PT+Sans+Narrow&display=swap">
<style>
:root{
  --orange:#f0a02b;
  --orange-dark:#e6901c;
  --blue:#2f74c8;
  --ink:#333;
  --muted:#9a9a9a;
  --title:#3a3a3a;
  --accent:#e08a10;
  --line:#e3e3e3;
  --footer:#3a3a3a;
  --footer-deep:#2b2b2b;
  --footer-text:#d8d8d8;
}
*{box-sizing:border-box;margin:0;padding:0}
html,body{width:701px;height:1200px;overflow:hidden}
body{position:relative;font-family:"Arimo",Arial,sans-serif;color:var(--ink);
  background:linear-gradient(180deg,#c9c2a8 0%,#8d8a7c 18%,#d9d4c4 40%,#7f8070 62%,#8a6a3c 80%,#5c4a30 100%)}
.abs{position:absolute}
.top-stripe{left:0;top:0;width:701px;height:3px;background:var(--orange)}
.brand{left:86px;top:30px;display:flex;align-items:center;gap:6px}
.brand-dot{width:18px;height:18px;border-radius:50%;background:var(--orange)}
.brand-name{font-family:"Noto Serif",serif;font-size:9px;color:#fff;width:120px;line-height:1.25}
.social-top{left:522px;top:24px;display:flex;gap:4px}
.social-top span{width:16px;height:16px;background:#7d8694;border-radius:2px}
.contact-line{right:86px;font-size:8px;color:#fff;display:flex;align-items:center;gap:5px}
.panel{left:77px;top:94px;width:547px;height:920px;background:#fff}
.nav{left:82px;top:98px;width:537px;height:34px;background:var(--orange);display:flex}
.nav a{flex:1;color:#fff;text-decoration:none;font-size:8.5px;display:flex;align-items:center;justify-content:center}
.nav a.active{background:var(--blue);flex:0 0 71px}
.hero{left:82px;top:133px;width:537px;height:228px;background:radial-gradient(ellipse at 55% 55%,#7a5a36 0%,#3a2818 35%,#0d0b0a 75%)}
.hero-arrow{top:230px}
h2.title{position:absolute;font-family:"Noto Serif",serif;font-weight:400;font-size:14px;color:var(--title)}
.copy{font-size:6.4px;line-height:13.6px;color:var(--muted)}
.photo{position:absolute}
.staff-name{font-size:8.5px;color:var(--accent)}
.divider{height:1px;background:var(--line)}
.calendar{left:449px;top:406px;width:168px;height:143px;background:#2a2a2a;border-radius:3px;padding:4px}
.cal-head{height:14px;display:flex;align-items:center;justify-content:space-between;color:#fff;font-size:6.5px;font-weight:700;padding:0 3px}
.cal-head i{width:9px;height:9px;border-radius:50%;background:#555;display:block}
.cal-grid{display:grid;grid-template-columns:repeat(7,1fr);gap:1px;background:#bbb;margin-top:2px}
.cal-grid span{background:#e9e9e9;height:15.5px;font-size:6.2px;display:flex;align-items:center;justify-content:center;color:#222;font-weight:700}
.cal-grid span.dow{background:#d4d4d4;height:11px;font-weight:400;font-style:italic;color:#444}
.cal-grid span.off{color:#aaa;font-weight:400}
.cal-grid span.today{background:var(--blue);color:#fff}
.event{left:450px;width:170px}
.event-title{display:flex;align-items:center;gap:6px;font-size:8.5px;color:#555}
.event-meta{font-size:6px;font-style:italic;color:#444;margin-top:6px}
.event-meta b{color:var(--blue);font-weight:700}
.event-copy{font-size:6px;line-height:11px;color:var(--muted);margin-top:6px}
.prayer{left:442px;top:782px;width:176px;height:210px;border:1px solid var(--line)}
.field{position:absolute;left:11px;width:152px;height:20px;border:1px solid #d6d6d6;font-size:6px;color:#777;padding:6px 8px}
.send{position:absolute;left:49px;top:177px;width:76px;height:22px;background:var(--orange);color:#fff;font-size:8px;display:flex;align-items:center;justify-content:center}
.footer{left:0;top:1022px;width:701px;height:136px;background:var(--footer)}
.footer-bottom{left:0;top:1158px;width:701px;height:42px;background:var(--footer-deep)}
.f-title{font-family:"PT Sans Narrow",sans-serif;font-size:12px;color:#e8e8e8}
.f-copy{font-size:5.8px;color:var(--footer-text);line-height:12px}
.f-list li{list-style:none;position:relative;padding-left:10px;margin-bottom:6px}
.f-list li::before{content:"";position:absolute;left:0;top:4px;width:4px;height:4px;border-radius:50%;background:#bbb}
.hours{font-size:5.8px;color:var(--footer-text);border-collapse:collapse}
.hours td{height:14.8px;padding:0}
.hours td:first-child{width:53px}
.news-input{left:411px;top:1085px;width:147px;height:21px;border:1px solid #666;font-size:5.8px;color:#bbb;padding:7px 8px}
.subscribe{left:412px;top:1116px;width:65px;height:21px;background:var(--blue);color:#fff;font-size:7px;display:flex;align-items:center;justify-content:center}
.donate-pill{left:533px;top:1118px;width:85px;height:15px;border-radius:8px;background:#f4b73a;font-size:6.5px;font-weight:700;color:#1f3a6e;display:flex;align-items:center;justify-content:center}
.cards{left:539px;top:1139px;display:flex;gap:3px}
.cards span{width:23px;height:13px;background:#e6e6e6;border-radius:1px}
.social-foot{left:533px;top:1171px;display:flex;gap:4px}
.social-foot span{width:18px;height:18px;border-radius:50%;border:1px solid #888}
.copyright{left:82px;top:1176px;font-size:5.8px;color:#bbb}
</style>
</head>
<body>
<div class="abs top-stripe"></div>

<div class="abs brand"><span class="brand-dot"></span><span class="brand-name">Harvest Gateway Fellowship Ministries</span></div>

<div class="abs social-top" aria-label="Social media links"><span></span><span></span><span></span><span></span><span></span></div>
<div class="abs contact-line" style="top:52px">
  <svg width="11" height="8" viewBox="0 0 11 8"><rect x=".5" y=".5" width="10" height="7" fill="none" stroke="#fff"/><path d="M.5 .5 5.5 4.5 10.5 .5" fill="none" stroke="#fff"/></svg>
  Email : info@harvestgateway.org</div>
<div class="abs contact-line" style="top:70px">
  <svg width="11" height="8" viewBox="0 0 11 8"><path d="M1 3c0-2 9-2 9 0v1H7V3H4v1H1z M2 4h7l1 4H1z" fill="#fff"/></svg>
  Call Us : 555.210.4830</div>

<div class="abs panel"></div>

<nav class="abs nav">
  <a class="active" href="#">Home</a><a href="#">About Us</a><a href="#">Events</a><a href="#">Prayer Request</a><a href="#">Donate</a><a href="#">Contact Us</a>
</nav>

<div class="abs hero" role="img" aria-label="Slideshow photo: hands holding an open Bible with a rosary"></div>
<svg class="abs hero-arrow" style="left:92px" width="12" height="40" viewBox="0 0 12 40"><path d="M11 1 1 20 11 39" fill="none" stroke="#fff" stroke-width="2"/></svg>
<svg class="abs hero-arrow" style="left:597px" width="12" height="40" viewBox="0 0 12 40"><path d="M1 1 11 20 1 39" fill="none" stroke="#fff" stroke-width="2"/></svg>

<h2 class="title" style="left:84px;top:373px">Welcome to Our Church</h2>
<div class="photo" style="left:82px;top:403px;width:124px;height:99px;background:linear-gradient(160deg,#6e6a66,#b89a70 55%,#4a3b2c)" role="img" aria-label="Photo of a crucifix against an evening sky"></div>
<p class="abs copy" style="left:224px;top:404px;width:206px">Welcome to Harvest Gateway Fellowship Ministry, a place where we can come together and fellowship. HGFM is located in Millbrook, Kansas and we would love to have you worship with us. We believe God is doing something extraordinary through our church and would like for you to be a part. Please prayerfully consider our church as a place you would like to worship and fellowship with us as we continue to grow.place you would like to worship........</p>
<p class="abs copy" style="left:82px;top:507px;width:350px">Welcome to Harvest Gateway Fellowship Ministry, a place where we can come together and fellowship. HGFM is you would like to worship and fellowship with us as we continue to grow.place you would like to worship........</p>

<h2 class="title" style="left:446px;top:373px">Upcoming Events</h2>
<div class="abs calendar">
  <div class="cal-head"><i></i>June, 2014<i></i></div>
  <div class="cal-grid">
    <span class="dow">Sun</span><span class="dow">Mon</span><span class="dow">Tue</span><span class="dow">Wed</span><span class="dow">Thu</span><span class="dow">Fri</span><span class="dow">Sat</span>
    <span class="off">27</span><span class="off">28</span><span class="off">29</span><span class="off">30</span><span>1</span><span>2</span><span>3</span>
    <span>4</span><span>5</span><span class="today">6</span><span>7</span><span>8</span><span>9</span><span>10</span>
    <span>11</span><span>12</span><span>13</span><span>14</span><span>15</span><span>16</span><span>17</span>
    <span>18</span><span>19</span><span>20</span><span>21</span><span>22</span><span>23</span><span>24</span>
    <span>25</span><span>26</span><span>27</span><span>28</span><span>29</span><span>30</span><span>31</span>
    <span class="off">1</span><span class="off">2</span><span class="off">3</span><span class="off">4</span><span class="off">5</span><span class="off">6</span><span class="off">7</span>
  </div>
</div>

<div class="abs event" style="top:562px">
  <div class="event-title"><svg width="11" height="10" viewBox="0 0 11 10"><rect x=".5" y="1.5" width="10" height="8" fill="none" stroke="#666"/><rect x=".5" y="1.5" width="10" height="2" fill="#666"/></svg>Etiam tristique tristique dui.</div>
  <div class="event-meta">June 08, 2012 &nbsp;/&nbsp; <b>2 Comments</b></div>
  <div class="event-copy">I can help you protect your assets and legacy using Last and Testaments, Trusts,.....</div>
</div>
<div class="abs divider" style="left:446px;top:624px;width:176px"></div>
<div class="abs event" style="top:636px">
  <div class="event-title"><svg width="11" height="10" viewBox="0 0 11 10"><rect x=".5" y="1.5" width="10" height="8" fill="none" stroke="#666"/><rect x=".5" y="1.5" width="10" height="2" fill="#666"/></svg>Etiam tristique tristique dui.</div>
  <div class="event-meta">June 08, 2012 &nbsp;/&nbsp; <b>2 Comments</b></div>
  <div class="event-copy">I can help you protect your assets and legacy using Last and Testaments, Trusts,.....</div>
</div>
<div class="abs divider" style="left:446px;top:699px;width:176px"></div>
<div class="abs event" style="top:711px">
  <div class="event-title"><svg width="11" height="10" viewBox="0 0 11 10"><rect x=".5" y="1.5" width="10" height="8" fill="none" stroke="#666"/><rect x=".5" y="1.5" width="10" height="2" fill="#666"/></svg>Etiam tristique tristique dui.</div>
  <div class="event-meta">June 08, 2012 &nbsp;/&nbsp; <b>2 Comments</b></div>
  <div class="event-copy">I can help you protect your assets and legacy using Last and Testaments, Trusts,.....</div>
</div>
<div class="abs divider" style="left:446px;top:773px;width:176px"></div>

<h2 class="title" style="left:84px;top:557px">Our Staff</h2>
<div class="photo" style="left:82px;top:590px;width:68px;height:64px;background:linear-gradient(180deg,#f1f1f1,#cfcfcf 60%,#2a2a2a)" role="img" aria-label="Portrait of the pastor"></div>
<div class="abs staff-name" style="left:163px;top:589px">Pastor Daniel Okafor</div>
<p class="abs copy" style="left:164px;top:606px;width:264px">As you venture on our website please feel free to contact us through email, phone, or leave a prayer request for us to pray on your behalf. Please take a minute and look at our upcoming events.As you venture on our website please feel free to contact us through minute and look at our upcoming events.......</p>
<div class="abs divider" style="left:82px;top:666px;width:348px"></div>
<div class="photo" style="left:82px;top:678px;width:68px;height:64px;background:linear-gradient(180deg,#f1f1f1,#cfcfcf 60%,#2a2a2a)" role="img" aria-label="Portrait of the minister"></div>
<div class="abs staff-name" style="left:163px;top:677px">Minister Ruth Ellison</div>
<p class="abs copy" style="left:164px;top:694px;width:264px">As you venture on our website please feel free to contact us through email, phone, or leave a prayer request for us to pray on your behalf. Please take a minute and look at our upcoming events.As you venture on our website please feel free to contact us through minute and look at our upcoming events.......</p>

<h2 class="title" style="left:82px;top:791px">Donations</h2>
<div class="photo" style="left:82px;top:823px;width:170px;height:102px;background:radial-gradient(circle at 55% 55%,#9a8a6c,#3a322a 70%)" role="img" aria-label="Photo of money placed in an offering plate"></div>
<p class="abs copy" style="left:82px;top:932px;width:172px;line-height:14px">Matthew 25: 40<br>"The King will reply, 'Truly I tell you, whatever you did for one of the least of these brothers and sisters of mine, you did for me.'"The King will reply, 'Truly I tell you, whatever you did for one of the least of these brothers and sisters of mine, you did for me."</p>

<h2 class="title" style="left:261px;top:791px">Media</h2>
<div class="photo" style="left:261px;top:823px;width:170px;height:102px;background:linear-gradient(180deg,#c8c0b4,#6e6258 55%,#2e2a28)" role="img" aria-label="Video still of a congregation at a worship service"></div>
<svg class="abs" style="left:329px;top:857px" width="36" height="36" viewBox="0 0 36 36"><circle cx="18" cy="18" r="16" fill="rgba(0,0,0,.35)" stroke="#fff" stroke-width="2"/><path d="M14 11 25 18 14 25z" fill="#fff"/></svg>
<p class="abs copy" style="left:261px;top:932px;width:172px;line-height:14px">Matthew 25: 40<br>"The King will reply, 'Truly I tell you, whatever you did for one of the least of these brothers and sisters of mine, you did for me.'"The King will reply, 'Truly I tell you, whatever you did for one of the least of these brothers and sisters of mine, you did for me."</p>

<form class="abs prayer">
  <h2 class="title" style="right:10px;top:10px">Submit a Prayer Request</h2>
  <div class="field" style="top:40px">Name :</div>
  <div class="field" style="top:64px">Address :</div>
  <div class="field" style="top:90px">Prayer Title :</div>
  <div class="field" style="top:115px">Prayer Topic :<svg style="position:absolute;right:6px;top:7px" width="6" height="5" viewBox="0 0 6 5"><path d="M0 0h6L3 5z" fill="#555"/></svg></div>
  <div class="field" style="top:138px;height:32px">Comments :</div>
  <div class="send">Send Request</div>
</form>

<div class="abs footer"></div>
<div class="abs footer-bottom"></div>

<div class="abs f-title" style="left:82px;top:1032px">Contact Us</div>
<p class="abs f-copy" style="left:83px;top:1052px">Feel free to contact us if you have any problems.</p>
<ul class="abs f-copy f-list" style="left:83px;top:1073px;width:170px">
  <li>Address : 418 Elm Ave.,<br>Mailing Address: PO Box 72, Millbrook, KS</li>
  <li>Phone : 555.210.4830<br>Fax : 555.210.4831</li>
  <li>Email :info@harvestgateway.org</li>
</ul>

<div class="abs f-title" style="left:267px;top:1032px">Services Timings</div>
<table class="abs hours" style="left:268px;top:1052px">
  <tr><td>Monday:</td><td>10 am - 10 pm</td></tr>
  <tr><td>Tuesday:</td><td>10 am - 10 pm</td></tr>
  <tr><td>Wednesday:</td><td>10 am - 10 pm</td></tr>
  <tr><td>Thursday:</td><td>10 am - 10 pm</td></tr>
  <tr><td>Friday:</td><td>10 am - 10 pm</td></tr>
  <tr><td>Saturday:</td><td>10 am - 10 pm</td></tr>
  <tr><td>Sunday:</td><td>Holiday</td></tr>
</table>

<div class="abs f-title" style="left:411px;top:1032px">News letter</div>
<p class="abs f-copy" style="left:411px;top:1052px;width:150px">In venenatis neque a eros laoreet eu placerat erat suscipit. Fusce cursus, erat ut scelerisque condimentum</p>
<div class="abs news-input">Enter Your Email :</div>
<div class="abs subscribe">SUBSCRIBE</div>
<div class="abs donate-pill">Donate Online</div>
<div class="abs cards" aria-label="Accepted payment cards"><span></span><span></span><span></span></div>

<div class="abs copyright">Copyright 2014 Harvest Gateway.All Right Reserved.</div>
<div class="abs social-foot" aria-label="Social media links"><span></span><span></span><span></span><span></span></div>
</body>
</html>
```